Fernhale Business Card Design

We are looking for a fresh business card design for our new logo. We would like a business card that is unique but friendly. We are in the window coverings business offering blinds, shutters and shades for homes.

Target Market(s)

Targeting the end-consumer

Industry/Entity Type

Business

Requirements
Must have
• Must have a dedicates space for a photo of our sales person. Must contain our new logo (attached).

```html
<!DOCTYPE html>
<html lang="en">
<head>
<meta charset="utf-8">
<title>Fernhale Business Card</title>
<link rel="stylesheet" href="https://fonts.googleapis.com/css2?family=Alegreya:wght@500&family=Open+Sans:wght@400;600&display=swap">
<style>
  :root {
    --backdrop: #000000;
    --card-white: #ffffff;
    --brand-green: #8cc540;
    --photo-tone: #e6ecdd;
    --ink-grey: #5a595c;
    --ink-dark: #1d1d1f;
  }
  html, body {
    margin: 0;
    padding: 0;
    width: 1200px;
    height: 900px;
    overflow: hidden;
    background: var(--backdrop);
  }
  .stage {
    position: relative;
    width: 1200px;
    height: 900px;
  }
  .card {
    position: absolute;
    top: 275px;
    width: 477px;
    height: 294px;
    overflow: hidden;
  }
  .card-front {
    left: 116px;
    background: var(--card-white);
    border-radius: 0 56px 0 56px;
  }
  .card-back {
    left: 622px;
    background: var(--brand-green);
    border-radius: 56px 0 56px 0;
  }
  .brand {
    position: absolute;
    left: 30px;
    top: 70px;
    display: flex;
    align-items: center;
    gap: 16px;
  }
  .brand-square {
    width: 60px;
    height: 60px;
    box-sizing: border-box;
    border: 3px solid var(--ink-grey);
    border-radius: 6px;
  }
  .brand-name {
    font-family: "Alegreya", Georgia, serif;
    font-weight: 500;
    font-size: 50px;
    color: var(--ink-grey);
    line-height: 1;
  }
  .sales-photo {
    position: absolute;
    left: 30px;
    top: 150px;
    width: 96px;
    height: 116px;
    border-radius: 6px;
    background: linear-gradient(180deg, #eef2e8 0%, var(--photo-tone) 100%);
    border: 2px solid var(--brand-green);
    box-sizing: border-box;
  }
  .person {
    position: absolute;
    right: 19px;
    top: 34px;
    text-align: right;
    font-family: "Open Sans", Arial, sans-serif;
  }
  .person-name {
    font-weight: 600;
    font-size: 18px;
    color: var(--brand-green);
    line-height: 1.2;
  }
  .person-role {
    font-size: 12.5px;
    color: var(--ink-dark);
    line-height: 1.5;
  }
  .address {
    position: absolute;
    right: 21px;
    top: 157px;
    text-align: right;
    font-family: "Open Sans", Arial, sans-serif;
    font-size: 13px;
    line-height: 17px;
    color: var(--ink-dark);
  }
  .contacts {
    position: absolute;
    right: 19px;
    top: 217px;
    margin: 0;
    padding: 0;
    list-style: none;
    font-family: "Open Sans", Arial, sans-serif;
    font-size: 13px;
    line-height: 17.5px;
    color: var(--ink-dark);
  }
  .contacts li {
    display: flex;
    justify-content: flex-end;
    align-items: center;
    gap: 7px;
  }
  .contacts svg {
    width: 11px;
    height: 11px;
    fill: var(--brand-green);
  }
  .back-name {
    position: absolute;
    left: 0;
    right: 0;
    top: 118px;
    text-align: center;
    font-family: "Alegreya", Georgia, serif;
    font-weight: 500;
    font-size: 56px;
    color: var(--card-white);
    line-height: 1;
  }
</style>
</head>
<body>
<main class="stage">
  <section class="card card-front">
    <div class="brand">
      <div class="brand-square"></div>
      <span class="brand-name">Fernhale</span>
    </div>
    <div class="sales-photo" role="img" aria-label="Photo of the sales person"></div>
    <div class="person">
      <div class="person-name">Daniel Hart</div>
      <div class="person-role">Managing Director</div>
    </div>
    <div class="address">
      48 Linden Row, Suite 2<br>
      Northvale, 204518
    </div>
    <ul class="contacts">
      <li>044-987 654 321
        <svg viewBox="0 0 24 24" aria-hidden="true"><path d="M6.6 10.8a15.1 15.1 0 0 0 6.6 6.6l2.2-2.2c.3-.3.7-.4 1-.2 1.1.4 2.3.6 3.6.6.6 0 1 .4 1 1V20c0 .6-.4 1-1 1A17 17 0 0 1 3 4c0-.6.4-1 1-1h3.5c.6 0 1 .4 1 1 0 1.3.2 2.5.6 3.6.1.3 0 .7-.2 1z"/></svg>
      </li>
      <li>hello@fernhale.com
        <svg viewBox="0 0 24 24" aria-hidden="true"><path d="M2 5h20v14H2z M3.5 6.5 12 12.5l8.5-6z" fill-rule="evenodd"/></svg>
      </li>
      <li>www.fernhaleblinds.com
        <svg viewBox="0 0 24 24" aria-hidden="true"><path d="M10.6 13.4a1 1 0 0 1 0-1.4l4-4a1 1 0 1 1 1.4 1.4l-4 4a1 1 0 0 1-1.4 0zM8.5 20.5a5 5 0 0 1-3.5-8.5l2.5-2.5 1.4 1.4-2.5 2.5a3 3 0 0 0 4.2 4.2l2.5-2.5 1.4 1.4-2.5 2.5a5 5 0 0 1-3.5 1.5zm8-6-1.4-1.4 2.5-2.5a3 3 0 0 0-4.2-4.2l-2.5 2.5-1.4-1.4 2.5-2.5a5 5 0 0 1 7 7z"/></svg>
      </li>
    </ul>
  </section>

  <section class="card card-back">
    <div class="back-name">Fernhale</div>
  </section>
</main>
</body>
</html>
```